Beacon Advisory Website

I currently have a website www.beaconadvisoryinc.com. We are a IT Consulting Company. Our website will pretty much tell out our services. I am looking to enhance my website and make it look more professional. Looking for very classy and Contemporary look and design for my website.

It Company

```html
<!DOCTYPE html>
<html lang="en">
<head>
<meta charset="utf-8">
<title>Beacon Advisory</title>
<link href="https://fonts.googleapis.com/css2?family=Montserrat:wght@400;500;600&family=Open+Sans:ital,wght@0,400;0,600;1,400&display=swap" rel="stylesheet">
<style>
:root{
  --brand:#1a75c4;
  --brand-deep:#0d3f8a;
  --topbar:#1b5fa8;
  --ink:#222;
  --muted:#666;
  --soft:#f3f4f6;
  --hero:#eef0f2;
  --footer:#333333;
  --footer-bottom:#262626;
  --footer-text:#b5b5b5;
}
*{box-sizing:border-box;margin:0;padding:0}
html,body{width:1200px;height:2826px;overflow:hidden}
body{position:relative;font-family:"Open Sans",Arial,sans-serif;color:var(--ink);background:#fff}
.abs{position:absolute}
.topbar{left:0;top:0;width:1200px;height:42px;background:var(--topbar);color:#fff;font-size:14px}
.topbar .item{position:absolute;top:11px;display:flex;align-items:center;gap:8px}
.social{display:flex;gap:14px}
.social span{width:16px;height:16px;border-radius:50%;background:#fff;display:block}
.nav{left:0;top:42px;width:1200px;height:82px;background:#fff;box-shadow:0 1px 3px rgba(0,0,0,.08)}
.brand{position:absolute;left:80px;top:22px;display:flex;align-items:center;gap:10px}
.brand .mark{width:36px;height:36px;background:var(--brand);border-radius:4px}
.brand .name{font-family:Montserrat,sans-serif;font-weight:600;font-size:22px;color:var(--brand-deep)}
.menu{position:absolute;right:80px;top:30px;display:flex;gap:30px;font-family:Montserrat,sans-serif;font-size:15px;font-weight:500}
.menu .active{color:var(--brand)}
.hero{left:0;top:124px;width:1200px;height:532px;background:var(--hero)}
.hero h1{position:absolute;left:80px;top:130px;font-family:Montserrat,sans-serif;font-weight:500;font-size:60px;color:#2b2b2b}
.hero .tag{position:absolute;left:80px;top:205px;font-family:Montserrat,sans-serif;font-weight:500;font-size:21px;color:var(--brand)}
.hero p{position:absolute;left:80px;top:248px;font-size:14px;line-height:23px;color:#555;width:520px}
.btn{position:absolute;left:77px;top:339px;width:166px;height:51px;background:var(--brand);color:#fff;font-size:16px;display:flex;align-items:center;justify-content:center}
.hero .photo{position:absolute;left:660px;top:26px;width:240px;height:506px;background:linear-gradient(180deg,#d9cfc6,#8e8a86);border-radius:110px 110px 0 0}
.arrow{position:absolute;top:247px;width:41px;height:40px;display:flex;align-items:center;justify-content:center}
.arrow.prev{left:17px;background:#c9c9c9}
.arrow.next{left:1140px;background:var(--brand)}
.dots{position:absolute;left:570px;top:480px;display:flex;gap:10px}
.dots span{width:10px;height:10px;border-radius:50%;background:#bbb}
.dots span:first-child{background:var(--brand)}
.service{position:absolute;top:708px;width:360px;text-align:center}
.service .icon{width:106px;height:106px;border-radius:50%;border:2px solid var(--brand);margin:0 auto;display:flex;align-items:center;justify-content:center}
.service .icon.filled{background:var(--brand)}
.service h3{margin-top:22px;font-family:Montserrat,sans-serif;font-weight:500;font-size:24px}
.service p{margin-top:14px;height:69px;font-size:13.5px;line-height:23px;color:var(--muted);padding:0 4px}
.service .more{display:block;margin-top:14px;font-size:14px;color:#444}
.service .more.active{color:var(--brand)}
.section-title{position:absolute;left:0;width:1200px;text-align:center;font-family:Montserrat,sans-serif;font-weight:400;font-size:40px;color:#222}
.section-title b{font-weight:600;color:var(--brand-deep)}
.section-title .light{color:#555}
.divider{position:absolute;left:490px;width:220px;height:20px}
.about{left:0;top:1032px;width:1200px;height:418px;background:var(--soft)}
.devices{position:absolute;left:141px;top:136px;width:358px;height:282px;background:linear-gradient(160deg,#2a3440,#0f151c);border-radius:8px}
.about h4{position:absolute;left:625px;top:134px;font-size:20px;font-weight:400;color:#333}
.about p{position:absolute;left:625px;top:176px;width:500px;font-size:14px;line-height:22.5px;color:#555}
.filters{position:absolute;left:0;top:1604px;width:1200px;display:flex;justify-content:center;gap:60px;font-size:14px;color:#555}
.tile{position:absolute;top:1667px;width:300px;height:302px}
.tile.overlay{background:#2e8ed0;color:#fff;text-align:center}
.tile.overlay h5{margin-top:128px;font-family:Montserrat,sans-serif;font-weight:500;font-size:19px}
.tile.overlay span{display:block;margin-top:6px;font-style:italic;font-size:14px}
.testimonials{left:0;top:2063px;width:1200px;height:326px;background:var(--soft)}
.quote{position:absolute;top:168px;width:500px;height:110px}
.quote .avatar{position:absolute;left:0;top:0;width:106px;height:105px;background:linear-gradient(180deg,#c7d3dc,#8fa4b3)}
.quote .who{position:absolute;left:128px;top:2px;font-family:Montserrat,sans-serif;font-size:18px;font-weight:500}
.quote .who i{font-family:"Open Sans",sans-serif;font-size:13px;font-weight:400;color:#666;margin-left:8px}
.quote p{position:absolute;left:128px;top:34px;width:370px;font-size:14px;line-height:23px;color:#444}
.partners{left:0;top:2389px;width:1200px;height:145px;display:flex;align-items:center;justify-content:space-around;padding:0 70px}
.partners span{display:block;height:44px;background:#c8c8c8;border-radius:4px}
.footer{left:0;top:2534px;width:1200px;height:230px;background:var(--footer);color:var(--footer-text);font-size:14px}
.footer h6{position:absolute;top:28px;font-family:Montserrat,sans-serif;font-weight:500;font-size:20px;color:#fff}
.footer .line{position:absolute;display:flex;gap:14px;line-height:21px}
.blog{position:absolute;left:435px;display:flex;gap:12px}
.blog .thumb{width:52px;height:52px;border-radius:50%;background:#8a8a8a;flex:none}
.blog p{line-height:21px}
.blog em{font-style:normal;color:#fff;font-size:13px}
.subscribe{position:absolute;left:812px;top:124px;width:311px;height:50px;display:flex}
.subscribe .field{flex:1;background:#444;color:#aaa;font-style:italic;padding:14px 22px}
.subscribe .go{width:52px;background:var(--brand);display:flex;align-items:center;justify-content:center}
.bottom{left:0;top:2764px;width:1200px;height:62px;background:var(--footer-bottom);color:#aaa;font-size:13px}
.bottom .copy{position:absolute;left:79px;top:21px}
.bottom .copy b{font-weight:400;color:var(--brand)}
.bottom .social{position:absolute;right:80px;top:23px}
.bottom .social span{background:#888}
</style>
</head>
<body>

<header class="abs topbar">
  <div class="item" style="left:77px">
    <svg width="12" height="18" viewBox="0 0 12 18"><rect x="1" y="1" width="10" height="16" rx="2" fill="none" stroke="#fff" stroke-width="1.6"/><circle cx="6" cy="14" r="1" fill="#fff"/></svg>
    +1 (555) 314 2290
  </div>
  <div class="item" style="left:258px">
    <svg width="20" height="14" viewBox="0 0 20 14"><rect x="1" y="1" width="18" height="12" fill="none" stroke="#fff" stroke-width="1.6"/><path d="M1 1l9 7 9-7" fill="none" stroke="#fff" stroke-width="1.6"/></svg>
    info@beaconadvisory.com
  </div>
  <div class="item" style="left:853px">
    <svg width="18" height="16" viewBox="0 0 18 16"><path d="M1 8h10M7 4l4 4-4 4M11 1h6v14h-6" fill="none" stroke="#fff" stroke-width="1.8"/></svg>
    SIGN UP
  </div>
  <div class="item social" style="left:990px;top:13px"><span></span><span></span><span></span><span></span></div>
</header>

<nav class="abs nav">
  <div class="brand"><span class="mark"></span><span class="name">Beacon Advisory</span></div>
  <div class="menu">
    <span class="active">HOME</span><span>COMPANY</span><span>SERVICES</span><span>SOLUTIONS</span><span>RESOURCES</span><span>CAREER</span><span>CONTACT US</span>
  </div>
</nav>

<section class="abs hero">
  <h1>Beacon Advisory</h1>
  <div class="tag">LET YOUR BUSINESS GROW WITH US</div>
  <p>Lorem Ipsum is simply dummy text of the printing and typesetting industry. Lorem Ipsum has been the industry's standard.</p>
  <div class="btn">CONTACT US</div>
  <div class="photo" role="img" aria-label="Photo of a businesswoman in a grey suit with arms crossed"></div>
  <div class="arrow prev"><svg width="10" height="16" viewBox="0 0 10 16"><path d="M8 2L2 8l6 6" fill="none" stroke="#fff" stroke-width="2"/></svg></div>
  <div class="arrow next"><svg width="10" height="16" viewBox="0 0 10 16"><path d="M2 2l6 6-6 6" fill="none" stroke="#fff" stroke-width="2"/></svg></div>
  <div class="dots"><span></span><span></span><span></span></div>
</section>

<div class="service" style="left:63px">
  <div class="icon filled"><svg width="44" height="44" viewBox="0 0 44 44" fill="none" stroke="#fff" stroke-width="2"><path d="M22 10a9 9 0 0 0-5 16v4h10v-4a9 9 0 0 0-5-16z"/><path d="M18 34h8M22 2v4M8 8l3 3M36 8l-3 3M4 20h4M36 20h4"/></svg></div>
  <h3>Consulting</h3>
  <p>Beacon Advisory has certified professional consultants to work with you to help increase the business by providing IT services...</p>
  <span class="more active">READ MORE</span>
</div>
<div class="service" style="left:420px">
  <div class="icon"><svg width="44" height="44" viewBox="0 0 44 44" fill="none" stroke="#1a75c4" stroke-width="2"><circle cx="18" cy="14" r="7"/><path d="M5 36c0-8 6-13 13-13"/><circle cx="30" cy="31" r="7"/><path d="M27 31l2 2 4-4"/></svg></div>
  <h3>Staff Augmentation</h3>
  <p>For years Beacon Advisory has been offering our customers the ability to augment their existing staff with temporary highly skilled IT professionals...</p>
  <span class="more">READ MORE</span>
</div>
<div class="service" style="left:776px">
  <div class="icon"><svg width="44" height="44" viewBox="0 0 44 44" fill="none" stroke="#1a75c4" stroke-width="2"><circle cx="22" cy="22" r="14"/><circle cx="22" cy="22" r="6"/><path d="M22 2v8M22 34v8M2 22h8M34 22h8"/></svg></div>
  <h3>Offshore</h3>
  <p>Our Offshore development model has a unique distinction of providing efficient software solutions with cost and quality advantage...</p>
  <span class="more">READ MORE</span>
</div>

<section class="abs about">
  <div class="section-title" style="top:50px">About <b>BEACON</b> <span class="light">ADVISORY</span></div>
  <div class="devices" role="img" aria-label="Desktop monitor, tablet and phone showing the website"></div>
  <h4>Lorem Ipsum is simply dummy text of the</h4>
  <p>Lorem Ipsum is simply dummy text of the printing and typesetting industry. Lorem Ipsum has been the industry's standard dummy text ever since the 1500s, when an unknown printer took a galley of type and scrambled it to make a type specimen book. It has survived not only five centuries, but also the leap into electronic typesetting, remaining essentially unchanged. It was popularised in the 1960s with the release of Lumatype sheets containing Lorem Ipsum passages, and more recently with desktop publishing software like Folio PageCraft including versions of Lorem Ipsum.</p>
</section>

<div class="section-title" style="top:1496px">Our <b>PORTFOLIO</b></div>
<svg class="divider" style="top:1554px" viewBox="0 0 220 20"><path d="M0 10h90M130 10h90" stroke="#999" stroke-width="1"/><rect x="102" y="2" width="16" height="16" fill="#1a75c4"/></svg>
<div class="filters"><span>All</span><span>Dashboards</span><span>Data warehousing</span><span>BPM</span></div>
<div class="tile" style="left:0;background:linear-gradient(135deg,#5a5f66,#c9ccd0)" role="img" aria-label="Photo of colleagues reviewing work on a laptop"></div>
<div class="tile" style="left:300px;background:linear-gradient(135deg,#e6e3de,#8a7a6a)" role="img" aria-label="Photo of a smiling businesswoman holding a pencil"></div>
<div class="tile overlay" style="left:600px"><h5>Consulting Meeting</h5><span>Company name</span></div>
<div class="tile" style="left:900px;background:linear-gradient(135deg,#eef0f2,#9aa3ab)" role="img" aria-label="Photo of two men working at a laptop in an office"></div>

<section class="abs testimonials">
  <div class="section-title" style="top:52px">Our <b>TESTIMONIALS</b></div>
  <svg class="divider" style="top:107px" viewBox="0 0 220 20"><path d="M0 10h90M130 10h90" stroke="#999" stroke-width="1"/><rect x="102" y="2" width="16" height="16" fill="#1a75c4"/></svg>
  <div class="quote" style="left:77px">
    <div class="avatar" role="img" aria-label="Portrait photo of the client"></div>
    <div class="who">Ellen Ramsey<i>- General Manager</i></div>
    <p>"Lorem Ipsum is simply dummy text of the printing and typesetting industry. Lorem Ipsum has been the industry's standard dummy text ever since the 1500s."</p>
  </div>
  <div class="quote" style="left:624px">
    <div class="avatar" role="img" aria-label="Portrait photo of the client"></div>
    <div class="who">Adam Carver<i>- Accountant</i></div>
    <p>"Lorem Ipsum is simply dummy text of the printing and typesetting industry. Lorem Ipsum has been the industry's standard dummy text ever since the 1500s."</p>
  </div>
</section>

<div class="abs partners">
  <span style="width:150px"></span><span style="width:140px"></span><span style="width:115px"></span><span style="width:125px"></span><span style="width:160px"></span><span style="width:95px"></span>
</div>

<footer class="abs footer">
  <h6 style="left:79px">Contact Info</h6>
  <div class="line" style="left:79px;top:68px"><svg width="18" height="24" viewBox="0 0 18 24"><path d="M9 23S2 14 2 9a7 7 0 0 1 14 0c0 5-7 14-7 14z" fill="none" stroke="#aaa" stroke-width="1.6"/><circle cx="9" cy="9" r="2.5" fill="none" stroke="#aaa" stroke-width="1.6"/></svg><span>240 Harbor Lane, Suite 310<br>Riverside, NJ 07150</span></div>
  <div class="line" style="left:79px;top:130px"><svg width="20" height="20" viewBox="0 0 20 20"><path d="M4 2l4 4-2 3c1 2 3 4 5 5l3-2 4 4-3 3C8 19 1 12 1 5z" fill="none" stroke="#aaa" stroke-width="1.6"/></svg><span>+1 (555) 314 2290</span></div>
  <div class="line" style="left:79px;top:168px"><svg width="20" height="16" viewBox="0 0 20 16"><rect x="1" y="2" width="18" height="12" fill="none" stroke="#aaa" stroke-width="1.6"/><path d="M1 2l9 7 9-7" fill="none" stroke="#aaa" stroke-width="1.6"/></svg><span>info@beaconadvisory.com</span></div>

  <h6 style="left:435px">Blog</h6>
  <div class="blog" style="top:64px"><div class="thumb" role="img" aria-label="Author photo"></div><p>Lorem Ipsum is simply dummy text of the<br>printing and typesetting industry.<br><em>November 30, 2015</em></p></div>
  <div class="blog" style="top:136px"><div class="thumb" role="img" aria-label="Author photo"></div><p>Lorem Ipsum is simply dummy text of the<br>printing and typesetting industry.<br><em>December 5, 2014</em></p></div>

  <h6 style="left:812px">Newsletter</h6>
  <p class="abs" style="left:812px;top:68px;width:310px;line-height:21px">Sign up to get updates about innovative and extra utility new property developed by us.</p>
  <div class="subscribe"><div class="field">Type Here...</div><div class="go"><svg width="22" height="16" viewBox="0 0 22 16"><rect x="1" y="1" width="20" height="14" fill="none" stroke="#fff" stroke-width="1.6"/><path d="M1 1l10 8 10-8" fill="none" stroke="#fff" stroke-width="1.6"/></svg></div></div>
</footer>

<div class="abs bottom">
  <div class="copy">© <b>Beacon Advisory</b> 2016. All Rights Reserved</div>
  <div class="social"><span></span><span></span><span></span><span></span></div>
</div>

</body>
</html>
```